Halvorsen Construction Needs a Business Card

Our current business card is very bland, and since we have a new logo, we would like a new business card design to reflect our company. It can be a single-sided or two-sided card, but it is important that our contact information appears on the same side. I am attaching a copy of our old card and our new logo. If you need the logo in another format than the one I'm sending, please let me know. This is the information that we must have on our card, but not necessarily in any specific order:
1) Our logo
2) General Contractor
3) Derek Halvorsen, Owner
4) 482 Commerce Ridge Road, Brenford, Alabama 35871
5) Office: 256-384-7150
7) Fax: 256-384-7151
8) Cell: 256-619-7150
9) halvorsenconstruction@qrm.net
10) halvorsenconstruction.com (can be omitted if necessary)
Also, I will need files in a format that I can alter if any of the above information changes in the near future. Thank you in advance for your submissions!
Target Market(s)
Commercial and residential clients, architects, and subcontractors.
Industry/Entity Type
Business

```html
<!DOCTYPE html>
<html lang="en">
<head>
<meta charset="utf-8">
<title>Halvorsen Construction – Business Card</title>
<link rel="stylesheet" href="https://fonts.googleapis.com/css2?family=Fira+Sans:wght@400;800&display=swap">
<style>
  :root {
    --ink: #0d0d0d;
    --paper: #ffffff;
    --steel-blue: #4f8eb1;
    --amber: #f7c244;
    --white-text: #ffffff;
  }
  html, body {
    margin: 0;
    padding: 0;
    overflow: hidden;
    background: var(--paper);
  }
  .card {
    position: relative;
    width: 1200px;
    height: 658px;
    overflow: hidden;
    background: var(--paper);
    font-family: "Fira Sans", Arial, sans-serif;
  }
  .brand-band {
    position: absolute;
    inset: 0 0 auto 0;
    height: 219px;
    background: var(--paper);
  }
  .brand-square {
    position: absolute;
    left: 136px;
    top: 0;
    width: 212px;
    height: 182px;
    background: var(--ink);
  }
  .brand-name {
    position: absolute;
    left: 374px;
    top: 16px;
    margin: 0;
    color: var(--ink);
    font-weight: 800;
    line-height: 1;
    white-space: nowrap;
  }
  .brand-name .word-main {
    display: block;
    font-size: 98px;
    letter-spacing: 15px;
  }
  .brand-name .word-sub {
    display: block;
    margin-top: -8px;
    font-size: 44px;
    letter-spacing: 27px;
  }
  .tagline {
    position: absolute;
    left: 584px;
    top: 156px;
    margin: 0;
    font-size: 38px;
    font-weight: 400;
    color: var(--ink);
    letter-spacing: 3px;
    line-height: 1;
    white-space: nowrap;
  }
  .info-band {
    position: absolute;
    left: 0;
    right: 0;
    top: 219px;
    bottom: 0;
    background: var(--steel-blue);
  }
  .person {
    position: absolute;
    left: 97px;
    top: 370px;
    color: var(--white-text);
  }
  .person-name {
    margin: 0;
    font-size: 37px;
    font-weight: 400;
    line-height: 1.05;
  }
  .person-role {
    margin: 0;
    font-size: 29px;
    font-weight: 400;
    line-height: 1;
  }
  .contact-list {
    position: absolute;
    left: 420px;
    top: 281px;
    margin: 0;
    display: grid;
    grid-template-columns: 176px auto;
    column-gap: 42px;
    font-size: 29px;
    line-height: 38.7px;
    white-space: nowrap;
  }
  .contact-list dt {
    text-align: right;
    color: var(--amber);
  }
  .contact-list dd {
    margin: 0;
    color: var(--white-text);
  }
</style>
</head>
<body>
  <main class="card">
    <header class="brand-band">
      <div class="brand-square" aria-hidden="true"></div>
      <h1 class="brand-name">
        <span class="word-main">HALVORSEN</span>
        <span class="word-sub">CONSTRUCTION</span>
      </h1>
      <p class="tagline">GENERAL CONTRACTOR</p>
    </header>

    <section class="info-band"></section>

    <div class="person">
      <p class="person-name">Derek Halvorsen</p>
      <p class="person-role">Owner</p>
    </div>

    <dl class="contact-list">
      <dt>office</dt><dd>256-384-7150</dd>
      <dt>fax</dt><dd>256-384-7151</dd>
      <dt>cell</dt><dd>256-619-7150</dd>
      <dt>address</dt><dd>482 Commerce Ridge Road, Brenford,</dd>
      <dt></dt><dd>Alabama 35871</dd>
      <dt>email</dt><dd>halvorsenconstruction@qrm.net</dd>
      <dt>www</dt><dd>halvorsenconstruction.com</dd>
    </dl>
  </main>
</body>
</html>
```